New Banner Ad Design Project

We are a start-up in San Francisco that sells consignment clothes with a percentage of the proceeds donated to charity. Also, volunteer groups can conduct dress drives and send them to us and we will sell them and give their charity back 60% of the proceeds.

We have several uses for banners:
- Home page banner:
- Promote timely Flash Sales (they last only 96 hours) which happen 2x/week
- Promote how good it feels to give back and shop
- Promote any special promotions such as a Gift With Purchase
- Community banner:
- Promote the lifestyle
- Promote any particular group conducting a dress drive

If you are going to submit one banner it is to be for an upcoming sale, as the two attached files address (maternity sale). If we find the right designer we will consider working with them beyond the design contest for future sale banners as well as others

We consider our 'competitors' to be The Garment Venture, The TrueCloset, WeavTurn, KnitRise, WearAgain. Our key differentiator is the charitable components and how groups are conducting dress drives to raise money.

We are in the midst of changing our company name, tagline and logo. The new company will be called 'LunaTessa' and our tagline is 'Rewoven Kindness'

Target Market(s)

Our initial audience is young women 16 - 30. We will be focusing on Prom February through May which appeals to 16 - 18 year olds.

We also have maternity-wear. We want these women to feel fashionable

We are focused on individuals who want to give back.

Industry/Entity Type

Charity

Font styles to use
Serif
Sans Serif

Colors
8769ae
1b1b1b
474747
c3c3c3
86cfc6
b7a5cd

Requirements
Must have
• - Youthful and stylish voice (not to be confused with Young)
- Appealing visuals
- Powerful call-to-action as it pertains to banners for our flash sales
- An inclusive feel
- Communicates our charitable component
Nice to have
• - Emotional appeal
- Women wearing our clothes (see attached)
Should not have
• - Too much text
- Too girly; overly flowery

```html
<!DOCTYPE html>
<html lang="en">
<head>
<meta charset="utf-8">
<title>Valentines Sale Banner</title>
<link href="https://fonts.googleapis.com/css2?family=Raleway:wght@200;300;400&family=Amatic+SC:wght@400;700&display=swap" rel="stylesheet">
<style>
  :root {
    --canvas: #ffffff;
    --card: #e4ddd2;
    --ink: #1b1b1b;
    --ink-soft: #2e2e2e;
    --accent: #f2354f;
    --dash: #3a3a3a;
    --photo-light: #c9c9c5;
    --photo-mid: #8e8d88;
    --photo-dark: #4a4a46;
  }
  html, body {
    margin: 0;
    padding: 0;
    width: 1200px;
    height: 553px;
    overflow: hidden;
    background: var(--canvas);
  }
  .banner {
    position: relative;
    width: 1200px;
    height: 553px;
    overflow: hidden;
    background: var(--canvas);
    font-family: "Raleway", sans-serif;
    color: var(--ink);
  }
  .banner__photo {
    position: absolute;
    left: 9px;
    top: 70px;
    width: 1182px;
    height: 483px;
    background:
      linear-gradient(180deg, rgba(255,255,255,1) 0%, rgba(255,255,255,0) 40%),
      linear-gradient(160deg, var(--photo-light) 0%, var(--photo-mid) 55%, var(--photo-dark) 100%);
  }
  .promo-card {
    position: absolute;
    left: 40px;
    top: 9px;
    width: 533px;
    height: 534px;
    background: var(--card);
    text-align: center;
  }
  .promo-card__border {
    position: absolute;
    inset: 9px;
    border: 1.5px dashed var(--dash);
  }
  .promo-card__lead {
    position: absolute;
    top: 26px;
    left: 0;
    right: 0;
    display: flex;
    align-items: center;
    justify-content: center;
    gap: 12px;
    font-weight: 400;
    font-size: 26px;
    line-height: 30px;
    color: var(--ink-soft);
    text-transform: uppercase;
  }
  .rule-double {
    width: 80px;
    height: 7px;
    border-top: 2.5px solid var(--ink);
    border-bottom: 2.5px solid var(--ink);
  }
  .promo-card__occasion {
    position: absolute;
    top: 58px;
    left: 0;
    right: 0;
    font-family: "Amatic SC", cursive;
    font-weight: 400;
    font-size: 86px;
    line-height: 90px;
    letter-spacing: 4px;
    color: var(--accent);
    text-transform: uppercase;
  }
  .promo-card__offer {
    position: absolute;
    top: 160px;
    left: 0;
    right: 0;
    font-weight: 400;
    font-size: 21px;
    line-height: 24px;
    text-transform: uppercase;
  }
  .promo-card__headline {
    position: absolute;
    top: 196px;
    left: 0;
    right: 0;
    font-weight: 200;
    font-size: 134px;
    line-height: 120px;
    letter-spacing: 2px;
    text-transform: uppercase;
  }
  .giving {
    position: absolute;
    top: 360px;
    left: 58px;
    display: flex;
    align-items: center;
    gap: 4px;
    text-align: left;
  }
  .giving__figure {
    font-weight: 300;
    font-size: 78px;
    line-height: 80px;
  }
  .giving__text {
    font-weight: 400;
    font-size: 18px;
    line-height: 24.5px;
    text-transform: uppercase;
  }
  .promo-card__cta {
    position: absolute;
    top: 485px;
    left: 0;
    right: 0;
    display: flex;
    align-items: center;
    justify-content: center;
    gap: 2px;
    font-weight: 400;
    font-size: 19px;
    line-height: 24px;
    color: var(--accent);
    text-transform: uppercase;
  }
  .promo-card__cta svg { display: block; }
</style>
</head>
<body>
  <div class="banner">
    <div class="banner__photo" role="img" aria-label="Black and white photo of a young woman in a polka-dot dress, hat and sunglasses, sitting on a hay bale in a field"></div>

    <section class="promo-card">
      <div class="promo-card__border"></div>

      <p class="promo-card__lead" style="margin:0">
        <span class="rule-double"></span>
        Treat yourself this
        <span class="rule-double"></span>
      </p>

      <h2 class="promo-card__occasion" style="margin:0">Valentines</h2>

      <p class="promo-card__offer" style="margin:0">With our up to 40% off</p>

      <h1 class="promo-card__headline" style="margin:0">Sale</h1>

      <div class="giving">
        <span class="giving__figure">60%</span>
        <span class="giving__text">Of the proceeds will be<br>donated to help build<br>futures worldwide</span>
      </div>

      <p class="promo-card__cta" style="margin:0">
        Spread the love this valentines
        <svg width="42" height="36" viewBox="0 0 42 36" aria-hidden="true">
          <path d="M21 33 C 10 24, 3 18, 4 10 C 5 4, 13 2, 17 8 C 19 11, 20 12, 21 14 C 23 8, 29 2, 35 4 C 41 7, 39 16, 33 22 C 29 26, 25 29, 21 33 Z" fill="none" stroke="var(--accent)" stroke-width="1.6" stroke-linejoin="round"/>
        </svg>
      </p>
    </section>
  </div>
</body>
</html>
```